Business Card Design

We need a design for business cards for our company. We have a logo. We teach EMT's and we are based out of Virginia. The information that will need to add would be, name, title, phone number, email, address. On the back of the business card would be "We help you, help others"

Target Market(s)

People that want to become EMT's

Colors

Designer to choose colors to be used in the design.

Requirements
Must have
• company logo

```html
<!DOCTYPE html>
<html lang="en">
<head>
<meta charset="utf-8">
<title>Crestline Medic Training – Business Card</title>
<link href="https://fonts.googleapis.com/css2?family=Roboto:wght@400;700&display=swap" rel="stylesheet">
<style>
  :root {
    --stage: #3a3a3a;
    --paper: #ffffff;
    --navy: #1c2532;
    --red: #c8202f;
    --grey: #949599;
    --grey-dark: #6c6e72;
    --grey-light: #b4b6ba;
  }
  * { margin: 0; padding: 0; box-sizing: border-box; }
  html, body {
    width: 1200px; height: 900px; overflow: hidden;
    background: var(--stage);
    font-family: "Roboto", Arial, sans-serif;
  }
  .sheet {
    position: relative; width: 1200px; height: 900px;
    display: flex; align-items: center; justify-content: center; gap: 50px;
  }
  .card {
    position: relative; overflow: hidden; flex: none;
    box-shadow: 0 10px 30px rgba(0,0,0,.45);
  }
  .card-front { width: 380px; height: 676px; background: var(--paper); }
  .card-back {
    width: 640px; height: 360px; background: var(--navy);
    display: flex; flex-direction: column; align-items: center; justify-content: center; gap: 18px;
  }

  .brand { display: flex; align-items: center; gap: 8px; }
  .brand-dot { width: 12px; height: 12px; border-radius: 50%; background: var(--red); flex: none; }
  .brand-name { color: var(--red); font-weight: 700; text-transform: uppercase; letter-spacing: .5px; white-space: nowrap; }
  .card-front .brand { position: absolute; left: 34px; top: 40px; }
  .card-front .brand-name { font-size: 17px; }
  .card-back .brand-name { font-size: 30px; }
  .card-back .brand-dot { width: 20px; height: 20px; }

  .tagline { color: var(--grey-light); font-size: 15px; letter-spacing: 3px; text-transform: uppercase; }

  .accent-bar { position: absolute; left: 0; top: 104px; width: 7px; height: 28px; background: var(--red); }
  .holder { position: absolute; left: 34px; top: 104px; }
  .holder-name { color: var(--red); font-weight: 700; font-size: 22px; text-transform: uppercase; line-height: 1.15; }
  .holder-title { color: var(--grey-dark); font-size: 14px; margin-top: 2px; }

  .address { position: absolute; left: 34px; top: 172px; color: var(--grey-dark); font-size: 14px; line-height: 1.5; }
  .contacts { position: absolute; left: 34px; top: 232px; list-style: none; color: var(--grey-dark); font-size: 14px; line-height: 1.6; }
  .contacts li { display: flex; align-items: center; gap: 8px; }
  .contacts svg { width: 11px; height: 11px; flex: none; }
  .contacts .web-strong { color: var(--red); }

  .hero-graphic {
    position: absolute; left: 40px; right: 0; top: 340px; height: 290px;
    background: linear-gradient(150deg, var(--red) 0%, var(--red) 50%, var(--grey) 50%, var(--grey) 100%);
  }
</style>
</head>
<body>
<main class="sheet">
  <section class="card card-front" aria-label="Business card front">
    <div class="brand">
      <span class="brand-dot"></span>
      <span class="brand-name">Crestline Medic Training</span>
    </div>

    <span class="accent-bar"></span>
    <div class="holder">
      <p class="holder-name">Daniel Harper</p>
      <p class="holder-title">Director</p>
    </div>

    <p class="address">418 Harbor Lane<br>Millbrook, VA 22301</p>

    <ul class="contacts">
      <li>
        <svg viewBox="0 0 12 12"><path d="M3 1l2 2-1 1.5c.6 1.4 1.6 2.4 3 3L8.5 6.5l2 2-1.5 2C5 10 2 7 1.5 2.5z" fill="var(--red)"/></svg>
        555-014-2290
      </li>
      <li>
        <svg viewBox="0 0 12 12"><rect x="1" y="2.5" width="10" height="7" rx="1" fill="var(--red)"/><path d="M1.5 3l4.5 3.5L10.5 3" stroke="#fff" fill="none"/></svg>
        hello@crestlinemedic.com
      </li>
      <li>
        <svg viewBox="0 0 12 12"><circle cx="6" cy="6" r="5" fill="var(--red)"/><path d="M1 6h10M6 1c-2.5 3-2.5 7 0 10M6 1c2.5 3 2.5 7 0 10" stroke="#fff" stroke-width=".8" fill="none"/></svg>
        <span>www.<span class="web-strong">crestlinemedic</span>.com</span>
      </li>
    </ul>

    <div class="hero-graphic" role="img" aria-label="Large medical cross split by a heartbeat line, red above and grey below"></div>
  </section>

  <section class="card card-back" aria-label="Business card back">
    <div class="brand">
      <span class="brand-dot"></span>
      <span class="brand-name">Crestline Medic Training</span>
    </div>
    <p class="tagline">We help you, help others</p>
  </section>
</main>
</body>
</html>
```